Bork Ventures, Inc. Website redesign

Revamp the website, it is old and outdated. www.borkventuresinc.example

Target Market(s)

Information Technology Consulting and Staffing

Coding

Coded - Design and coding required

Number of Pages Required

5+ page

Colors

Designer to choose colors to be used in the design.

Requirements
Must have
• Outlined text boxes just like from the Tolvane.example site. A clean look

```html
<!DOCTYPE html>
<html lang="en">
<head>
<meta charset="utf-8">
<title>Bork Ventures, Inc.</title>
<link href="https://fonts.googleapis.com/css2?family=Montserrat:wght@400;500;600;700&family=Roboto:wght@300;400&display=swap" rel="stylesheet">
<style>
:root{
  --red:#b2001e;
  --navy:#1c3652;
  --ink:#4a5563;
  --bg:#edf2f8;
  --teal-a:#0b86b5;
  --teal-b:#1fe3d6;
  --footer:#102b48;
  --green:#3fd49b;
  --blue:#1d6ec4;
  --rose:#e6394f;
  --aqua:#15b2b6;
}
*{box-sizing:border-box;margin:0;padding:0}
html,body{width:1200px;height:2938px;overflow:hidden}
body{position:relative;background:var(--bg);font-family:"Roboto",Arial,sans-serif;font-weight:300;color:var(--ink)}
.abs{position:absolute}
h1,h2,h3,.nav a,.btn,.brand-name{font-family:"Montserrat",Arial,sans-serif}
.btn{position:absolute;background:var(--red);color:#fff;font-weight:600;font-size:14px;display:flex;align-items:center;justify-content:center;text-decoration:none}

/* header */
.brand{left:94px;top:26px}
.brand-mark{display:flex;align-items:center;gap:8px}
.brand-square{width:22px;height:22px;background:var(--red)}
.brand-name{font-weight:700;font-size:22px;color:var(--navy);letter-spacing:.5px}
.nav{top:30px;left:0;width:1200px;height:20px}
.nav a{position:absolute;color:#fff;font-size:12px;font-weight:600;text-decoration:none}

/* hero */
.hero-art{left:0;top:0}
.hero h1{position:absolute;left:94px;top:194px;font-size:31px;line-height:35px;font-weight:500;color:var(--navy)}
.hero p{position:absolute;left:94px;top:318px;width:340px;font-size:12.5px;line-height:19px}
.slider-dashes{left:94px;top:510px;display:flex;gap:10px}
.slider-dashes span{width:35px;height:2px;background:#b7c0cc}
.slider-dashes span.on{background:var(--red)}

/* services */
.service{position:absolute;top:625px;width:238px;height:324px;background:#fff;border:1px dashed;padding:0 24px}
.service .hex{position:absolute;left:18px;top:-38px}
.service h3{margin-top:64px;font-size:13.5px;font-weight:600;color:var(--navy)}
.service p{margin-top:12px;font-size:10.5px;line-height:18px;color:#555c66}
.more{display:block;margin-top:12px;font-family:"Montserrat",sans-serif;font-size:10.5px;font-weight:600;color:var(--red);text-decoration:none}

/* sections */
.split h2{position:absolute;font-size:31px;line-height:38px;font-weight:500;color:var(--navy)}
.split p{position:absolute;font-size:12.5px;line-height:19.5px}

/* news */
.news-head{top:1932px;left:0;width:1200px;text-align:center}
.news-head h2{font-size:31px;font-weight:500;color:var(--navy)}
.news-head p{margin:12px auto 0;width:740px;font-size:14px;line-height:20px;color:#2d3a48;font-weight:400}
.post{position:absolute;top:2058px;width:235px;height:387px;background:#fff}
.post .photo{height:177px;width:100%}
.post .date{position:absolute;left:17px;top:164px;height:26px;padding:0 12px 0 10px;border-radius:13px;background:var(--red);color:#fff;font-size:11px;font-weight:400;display:flex;align-items:center;gap:6px}
.post h3{margin:40px 18px 0;font-size:13.5px;font-weight:600;color:var(--navy)}
.post p{margin:8px 18px 0;font-size:10.8px;line-height:17px;color:#555c66}
.post .more{margin-left:18px;margin-top:10px}
.dots{top:2486px;left:572px;display:flex;gap:14px}
.dots span{width:8px;height:8px;border-radius:50%;border:1px solid var(--red)}
.dots span.on{background:var(--red)}

/* footer */
.footer{left:0;top:2542px;width:1200px;height:396px;background:var(--footer);color:#c7d1de}
.footer .f-brand{left:96px;top:96px}
.footer .f-brand .brand-name{color:#fff;font-size:24px}
.footer .f-about{left:96px;top:198px;width:236px;font-size:11px;line-height:17px}
.fcol{top:100px}
.fcol h4{font-family:"Montserrat",sans-serif;font-size:14px;font-weight:600;color:#fff;margin-bottom:22px}
.fcol li{list-style:none;font-size:11px;line-height:15px;margin-bottom:12px}
.fcol .icon-row{display:flex;gap:10px}
.footer .rule{left:94px;top:336px;width:1012px;height:1px;background:#2c4663}
.footer .copy{left:0;top:359px;width:1200px;text-align:center;font-size:10px;color:#6f819a}
.footer .copy span{color:var(--red)}
</style>
</head>
<body>

<!-- header -->
<div class="abs brand brand-mark"><span class="brand-square"></span><span class="brand-name">Bork Ventures</span></div>

<!-- hero -->
<section class="hero">
  <svg class="abs hero-art" width="1200" height="568" role="img" aria-label="Illustration of a developer at a computer surrounded by floating code language blocks">
    <defs><linearGradient id="heroGrad" x1="0" y1="0" x2="1" y2="1"><stop offset="0" stop-color="var(--teal-a)"/><stop offset="1" stop-color="var(--teal-b)"/></linearGradient></defs>
    <path d="M612 0 C560 70 540 150 560 215 C590 305 700 335 760 420 C792 468 790 530 788 568 L1200 568 L1200 0 Z" fill="url(#heroGrad)"/>
  </svg>
  <nav class="abs nav">
    <a style="left:655px">Home</a><a style="left:722px">About us</a><a style="left:805px">Services</a><a style="left:886px">Strategy</a><a style="left:966px">IT News</a><a style="left:1045px">Contact us</a>
  </nav>
  <h1>For over 20 + years<br>We have been Providing<br>Reliable IT Solutions</h1>
  <p>Bork Ventures, Inc. is an 8(a) innovative and rapidly growing full-service IT consulting firm. We provide our clients with cutting-edge technologies</p>
  <a class="btn" style="left:94px;top:395px;width:130px;height:37px">Know More</a>
  <div class="abs slider-dashes"><span class="on"></span><span></span><span></span></div>
</section>

<!-- services -->
<section class="services">
  <article class="service" style="left:94px;border-color:var(--green)">
    <svg class="hex" width="76" height="84"><polygon points="38,0 76,21 76,63 38,84 0,63 0,21" fill="var(--green)"/></svg>
    <h3>Hardware / Software Sales</h3>
    <p>We have access to multiple distributor partners throughout North America, as well as Elite Partner Status with many of the industry's marquee manufacturers (such as Corvane) to ensure you are receiving the most aggressive pricing possible. Additionally, we have team members that possess the history, relationships and back office support to help simplify the process.</p>
    <a class="more">Read More</a>
  </article>
  <article class="service" style="left:352px;border-color:var(--blue)">
    <svg class="hex" width="76" height="84"><polygon points="38,0 76,21 76,63 38,84 0,63 0,21" fill="var(--blue)"/></svg>
    <h3>Professional Services</h3>
    <p>Our team provides experienced leadership and guidance, utilizing the industry standard methodologies. We help you maintain a comprehensive view of strategy, governance, technology, people and process, to deliver more successful business outcomes. Our expertise is focused in the following service areas.</p>
    <a class="more">Read More</a>
  </article>
  <article class="service" style="left:611px;border-color:#f1aab6">
    <svg class="hex" width="76" height="84"><polygon points="38,0 76,21 76,63 38,84 0,63 0,21" fill="var(--rose)"/></svg>
    <h3>Technology Assessment</h3>
    <p>Experience has shown companies that perform objective, third-party technology assessments have proven to be instrumental in identifying weaknesses or breaches in their environments before they adversely impact their business.</p>
    <a class="more">Read More</a>
  </article>
  <article class="service" style="left:869px;border-color:var(--aqua)">
    <svg class="hex" width="76" height="84"><polygon points="38,0 76,21 76,63 38,84 0,63 0,21" fill="var(--aqua)"/></svg>
    <h3>Technology Consulting</h3>
    <p>Implementing quality solutions is more than applying technology to problems. You need experts with deep technical knowledge and broad industry experience to help you design and implement cost-effective, reliable and secure solutions that meet your business priorities—on budget and on time. Our expertise focuses on the three key services below.</p>
    <a class="more">Read More</a>
  </article>
</section>

<!-- thought leadership -->
<section class="split">
  <svg class="abs" style="left:0;top:995px" width="620" height="480" role="img" aria-label="Illustration of a team meeting around a table with laptops and a light bulb idea">
    <defs><linearGradient id="leadGrad" x1="0" y1="0" x2="0" y2="1"><stop offset="0" stop-color="var(--teal-a)"/><stop offset=".7" stop-color="#1aa6c8"/><stop offset="1" stop-color="var(--bg)"/></linearGradient></defs>
    <path d="M0 5 L470 5 C500 20 520 60 560 110 C600 170 575 260 520 330 C470 390 300 400 240 470 L0 470 Z" fill="url(#leadGrad)"/>
  </svg>
  <h2 style="left:611px;top:1058px">Bringing Thought Leadership<br>and Quality to Every Project</h2>
  <p style="left:611px;top:1153px;width:490px">Bork Ventures, Inc. is an 8(a) full-service IT consulting company based in the Washington, DC Metro area. We offer specialized, highly customized technology solutions for our customers located throughout the United States. Learn about our Services now. No two businesses are the same. We believe the technology supporting your business operations should align with your company. Every project begins with a thorough analysis of your current technology environment. We work with you to define the environment you want. Then we implement industry-proven practices that enable you to achieve your business objectives.</p>
  <a class="btn" style="left:611px;top:1339px;width:120px;height:38px">Read More</a>
</section>

<!-- strategy -->
<section class="split">
  <svg class="abs" style="left:560px;top:1464px" width="640" height="500" role="img" aria-label="Illustration of three businessmen carrying a large golden key toward a keyhole">
    <defs><linearGradient id="stratGrad" x1="0" y1="0" x2="0" y2="1"><stop offset="0" stop-color="var(--teal-a)"/><stop offset=".75" stop-color="#1ab0cf"/><stop offset="1" stop-color="var(--bg)"/></linearGradient></defs>
    <path d="M165 0 L640 0 L640 500 L420 500 C380 470 400 430 330 420 C200 400 90 390 72 300 C60 230 90 150 120 110 C150 70 160 40 165 0 Z" fill="url(#stratGrad)"/>
  </svg>
  <h2 style="left:94px;top:1546px">Our Strategy Your Path to Success</h2>
  <p style="left:94px;top:1605px;width:505px">Civilian and Federal agencies are facing increased demands driven by the changing economic environment and shifts in the way products and services are sold and delivered. These factors have created an imperative to leverage new and innovative technology solution architectures like cloud computing to help reduce cost and deliver profit-driving IT capabilities faster than ever before. Savvy businesses understand that technology investments cannot be made solely to enable internal and external operations</p>
  <a class="btn" style="left:94px;top:1748px;width:120px;height:38px">Read More</a>
</section>

<!-- news -->
<section>
  <div class="abs news-head">
    <h2>IT News</h2>
    <p>Lorem ipsum dolor sit amet, consectetur adipiscing elit. Duis sed pellentesque massa. Curabitur viverra imperdiet sapien, nec ullamcorper sapien. Nullam pharetra maximus tellus</p>
  </div>
  <article class="post" style="left:94px">
    <div class="photo" role="img" aria-label="Photo of two businessmen reviewing documents at a desk" style="background:linear-gradient(135deg,#8593a6,#cfd6df)"></div>
    <span class="date"><svg width="11" height="10"><rect x=".5" y="1.5" width="10" height="8" fill="none" stroke="#fff"/><line x1="0" y1="4" x2="11" y2="4" stroke="#fff"/></svg>Aug. 21, 2019</span>
    <h3>Lorem ipsum dolor</h3>
    <p>Vivamus euismod nunc ut tristique mattis. Donec ulrics commodo pulvinar. Praesent malesuada ex fermentum sapien dapibus sagittis. In et egestas tellus. Vivamus placerat elit quam, vitae tempus augue mollis facilisis.</p>
    <a class="more">Read More....</a>
  </article>
  <article class="post" style="left:352px">
    <div class="photo" role="img" aria-label="Photo of colleagues discussing work at a laptop" style="background:linear-gradient(135deg,#6e7682,#d8dde3)"></div>
    <span class="date"><svg width="11" height="10"><rect x=".5" y="1.5" width="10" height="8" fill="none" stroke="#fff"/><line x1="0" y1="4" x2="11" y2="4" stroke="#fff"/></svg>Aug. 21, 2019</span>
    <h3>Lorem ipsum dolor</h3>
    <p>Vivamus euismod nunc ut tristique mattis. Donec ulrics commodo pulvinar. Praesent malesuada ex fermentum sapien dapibus sagittis. In et egestas tellus. Vivamus placerat elit quam, vitae tempus augue mollis facilisis.</p>
    <a class="more">Read More....</a>
  </article>
  <article class="post" style="left:611px">
    <div class="photo" role="img" aria-label="Photo of a presenter leading an office meeting" style="background:linear-gradient(135deg,#b7bcc0,#e7e8e6)"></div>
    <span class="date"><svg width="11" height="10"><rect x=".5" y="1.5" width="10" height="8" fill="none" stroke="#fff"/><line x1="0" y1="4" x2="11" y2="4" stroke="#fff"/></svg>Aug. 21, 2019</span>
    <h3>Lorem ipsum dolor</h3>
    <p>Vivamus euismod nunc ut tristique mattis. Donec ulrics commodo pulvinar. Praesent malesuada ex fermentum sapien dapibus sagittis. In et egestas tellus. Vivamus placerat elit quam, vitae tempus augue mollis facilisis.</p>
    <a class="more">Read More....</a>
  </article>
  <article class="post" style="left:870px">
    <div class="photo" role="img" aria-label="Photo of two women collaborating on a laptop" style="background:linear-gradient(135deg,#9aa6b8,#e4e6ea)"></div>
    <span class="date"><svg width="11" height="10"><rect x=".5" y="1.5" width="10" height="8" fill="none" stroke="#fff"/><line x1="0" y1="4" x2="11" y2="4" stroke="#fff"/></svg>Aug. 21, 2019</span>
    <h3>Lorem ipsum dolor</h3>
    <p>Vivamus euismod nunc ut tristique mattis. Donec ulrics commodo pulvinar. Praesent malesuada ex fermentum sapien dapibus sagittis. In et egestas tellus. Vivamus placerat elit quam, vitae tempus augue mollis facilisis.</p>
    <a class="more">Read More....</a>
  </article>
  <div class="abs dots"><span class="on"></span><span></span><span></span></div>
</section>

<!-- footer -->
<footer class="abs footer">
  <div class="abs f-brand brand-mark"><span class="brand-square"></span><span class="brand-name">Bork Ventures</span></div>
  <p class="abs f-about">Bork Ventures, Inc. is an 8(a) innovative and rapidly growing full-service IT consulting firm. We provide our clients with cutting-edge technologies and the know-how to apply them to their individual business models.</p>

  <div class="abs fcol" style="left:414px">
    <h4>Contact Us</h4>
    <ul>
      <li class="icon-row"><svg width="12" height="16"><path d="M6 1a5 5 0 0 1 5 5c0 4-5 9-5 9S1 10 1 6a5 5 0 0 1 5-5z" fill="none" stroke="var(--rose)" stroke-width="1.3"/><circle cx="6" cy="6" r="1.8" fill="var(--rose)"/></svg><span>Bork Ventures, Inc.<br>480 Quillby Lane<br>Ashford Vale, MD 20999</span></li>
      <li class="icon-row" style="margin-top:16px"><svg width="14" height="14"><path d="M3 1l3 3-2 2c1 2 2 3 4 4l2-2 3 3-2 2C6 13 1 8 1 3z" fill="none" stroke="var(--rose)" stroke-width="1.2"/></svg><span>555-014-2277 (Office)</span></li>
    </ul>
  </div>
  <div class="abs fcol" style="left:633px">
    <h4>Our Services</h4>
    <ul><li>Hardware / Software Sales</li><li>Professional Services</li><li>Technology Assessment</li><li>Technology Consulting</li></ul>
  </div>
  <div class="abs fcol" style="left:828px">
    <h4>Our Strategy</h4>
    <ul><li>Your Path to Success</li><li>These are the five pillars of<br>our successful IT strategy</li></ul>
  </div>
  <div class="abs fcol" style="left:1038px">
    <h4>Follow Us</h4>
    <ul>
      <li class="icon-row"><span style="width:10px;height:10px;background:#fff;display:inline-block;margin-top:2px"></span>Friendlane</li>
      <li class="icon-row"><span style="width:10px;height:10px;background:#fff;display:inline-block;margin-top:2px"></span>Worknet</li>
    </ul>
  </div>
  <div class="abs rule"></div>
  <div class="abs copy">© 2019 <span>Bork Ventures</span>. All Right Reserved.</div>
</footer>

</body>
</html>
```